Business Card Design

Just looking for a good designs that looks good with our company logo. I'd like it to be simple and to the point. Just including contact information, our logo, and my name somewhere on the card so future clients know who they're contacting, and a couple services offered. The two images I attached are pictures of our logo. I don't care which color they they are, I just attached both images to give a reference of logo colors depending on the color of the card.
Names: Carl Whitby
Phone: 816-555-0147
Email: greenstripeyard@fernmail.test
Services offered:
Mowing
Fertilization
Aeration
Bed & tree maintenance
and more.
Business
Names: Carl Whitby
Phone: 816-555-0147
(no website)

```html
<!DOCTYPE html>
<html lang="en">
<head>
<meta charset="utf-8">
<title>Greenstripe Yard Care – Business Card</title>
<link rel="stylesheet" href="https://fonts.googleapis.com/css2?family=Alegreya:wght@400;700&family=Oswald:wght@600&display=swap">
<style>
  :root {
    --stage: #d9d9d9;
    --card: #050505;
    --orange: #e8662a;
    --orange-deep: #d4521f;
    --bar-end: #2a1a14;
    --green: #2fa84a;
    --green-light: #7cc242;
    --green-dark: #1f7a34;
    --band-dark: #3a1420;
    --white: #f4f4f4;
  }
  * { margin: 0; padding: 0; box-sizing: border-box; }
  html, body { width: 1200px; height: 960px; overflow: hidden; }
  body {
    background: radial-gradient(circle at 50% 40%, #efefef, var(--stage) 75%);
    font-family: "Alegreya", Georgia, serif;
  }
  .card {
    position: absolute; left: 100px; top: 190px;
    width: 1000px; height: 580px;
    background: var(--card); overflow: hidden;
    box-shadow: 0 20px 40px rgba(0,0,0,.25);
  }
  .guarantee { position: absolute; left: 150px; top: 142px; display: flex; align-items: flex-end; }
  .guarantee__pct {
    font-family: "Oswald", Impact, sans-serif; font-weight: 600;
    color: var(--green-light); font-size: 34px; line-height: 1;
    position: relative; z-index: 1;
  }
  .guarantee__quality {
    position: absolute; left: 2px; top: 36px; background: var(--white);
    color: var(--green-dark); font-size: 10px; font-weight: 700; padding: 0 4px; letter-spacing: 1px;
  }
  .guarantee__band {
    margin-left: -6px; width: 200px; height: 32px;
    background: linear-gradient(90deg, var(--orange-deep), var(--band-dark) 85%);
    color: var(--white); font-family: "Oswald", Impact, sans-serif; font-weight: 600;
    font-size: 21px; line-height: 32px; padding-left: 22px;
  }
  .brand {
    position: absolute; left: 330px; top: 180px; width: 290px;
    display: flex; align-items: center; gap: 12px;
  }
  .brand__dot { width: 22px; height: 22px; border-radius: 50%; background: var(--orange); flex: none; }
  .brand__name { color: var(--orange); font-size: 31px; font-weight: 700; line-height: 1.1; }
  .contact { position: absolute; left: 630px; top: 100px; width: 330px; }
  .contact__bar {
    position: relative; display: flex; align-items: center; gap: 10px;
    background: linear-gradient(90deg, var(--orange) 0%, var(--orange-deep) 35%, var(--bar-end) 100%);
    color: var(--white); height: 40px; padding-left: 16px; margin-bottom: 22px;
  }
  .contact__bar::after {
    content: ""; position: absolute; right: 18px; top: 50%; width: 14px; height: 14px;
    margin-top: -7px; background: var(--green-dark);
  }
  .contact__bar--name { height: 48px; font-size: 28px; letter-spacing: 1px; }
  .contact__bar--phone { width: 300px; margin-left: 30px; font-size: 22px; }
  .contact__bar--email { width: 300px; margin-left: 30px; font-size: 15px; }
  .contact__icon { width: 22px; height: 22px; flex: none; }
  .services {
    position: absolute; left: 270px; top: 325px; width: 420px;
    text-align: center; font-size: 28px; line-height: 1.15; letter-spacing: .5px;
  }
  .services__line--green { color: var(--green); }
  .services__line--orange { color: var(--orange); }
  .landscape {
    position: absolute; left: 0; bottom: 0; width: 100%; height: 160px;
    background: linear-gradient(180deg, var(--green-light), var(--green-dark));
    border-radius: 55% 45% 0 0 / 40% 30% 0 0;
  }
</style>
</head>
<body>
  <article class="card">
    <div class="guarantee">
      <span class="guarantee__pct">100%</span>
      <span class="guarantee__quality">QUALITY</span>
      <span class="guarantee__band">Guaranteed</span>
    </div>

    <div class="brand">
      <span class="brand__dot"></span>
      <span class="brand__name">Greenstripe Yard Care</span>
    </div>

    <div class="contact">
      <div class="contact__bar contact__bar--name">Carl Whitby</div>
      <div class="contact__bar contact__bar--phone">
        <svg class="contact__icon" viewBox="0 0 24 24" aria-hidden="true">
          <rect width="24" height="24" rx="3" fill="#f4f4f4"/>
          <path d="M7 4l3 4-2 2c1 2.5 3.5 5 6 6l2-2 4 3-2 3c-6 0-13-7-13-13z" fill="#1f7a34"/>
        </svg>
        816-555-0147
      </div>
      <div class="contact__bar contact__bar--email">greenstripeyard@fernmail.test</div>
    </div>

    <p class="services">
      <span class="services__line--green">Mowing . Fertilization .Aeration</span><br>
      <span class="services__line--orange">Bed and tree maintenance</span><br>
      <span class="services__line--green">and more ...</span>
    </p>

    <div class="landscape" role="img" aria-label="Illustration of rolling green hills with a winding path and small trees"></div>
  </article>
</body>
</html>
```